Harbor Loom Floors Letterhead

Letterhead used for business reasons. It must be editable and easy to use.

Address is 2715 W. Pelican Lane Marlow Cove SC 34187 - 555.382.6519

```html
<!DOCTYPE html>
<html lang="en">
<head>
<meta charset="utf-8">
<title>Harbor Loom Floors Letterhead</title>
<link href="https://fonts.googleapis.com/css2?family=Lato:wght@400;700&family=Montserrat:wght@400&family=Great+Vibes&display=swap" rel="stylesheet">
<style>
  :root {
    --backdrop: #e4e4e4;
    --paper: #ffffff;
    --brand-orange: #e08a24;
    --brand-gray: #948a85;
    --ink: #1c1c1c;
    --ink-soft: #333333;
  }
  * { margin: 0; padding: 0; box-sizing: border-box; }
  html, body {
    width: 1200px; height: 1079px; overflow: hidden;
    background: var(--backdrop);
  }
  .letterhead {
    position: absolute;
    left: 232px; top: 20px;
    width: 735px; height: 1040px;
    background: var(--paper);
    box-shadow: 0 4px 16px rgba(0,0,0,0.18);
    font-family: 'Lato', sans-serif;
    color: var(--ink);
    overflow: hidden;
  }
  .brand-name {
    position: absolute; left: 37px; top: 44px;
    font-family: 'Lato', sans-serif;
    font-weight: 400;
    font-size: 30px; line-height: 34px;
    color: var(--brand-orange);
    width: 200px;
  }
  .contact {
    position: absolute; left: 531px; top: 81px;
    height: 54px; padding-left: 25px;
    border-left: 1.5px solid var(--brand-orange);
    font-family: 'Montserrat', sans-serif;
    font-style: normal;
    font-size: 13px; line-height: 17.5px;
    color: var(--ink-soft);
  }
  .contact .address { margin-top: -1px; }
  .contact .phone { margin-top: 8px; display: flex; align-items: center; gap: 5px; }
  .contact .phone svg { width: 11px; height: 11px; }
  .letter-body {
    position: absolute; left: 37px; top: 258px; width: 661px;
    font-size: 14.5px; line-height: 17.5px;
  }
  .date { margin-bottom: 18px; font-size: 15px; }
  .recipient { margin-bottom: 36px; }
  .recipient-company { margin-bottom: 36px; }
  .salutation { font-weight: 700; font-size: 19px; margin-bottom: 42px; }
  .paragraph {
    text-align: justify; font-size: 15.2px; line-height: 16.2px;
    margin-bottom: 16px;
  }
  .closing { margin-top: 38px; }
  .signature {
    position: absolute; left: 37px; top: 885px;
    font-family: 'Great Vibes', cursive;
    font-size: 36px; color: var(--ink);
  }
  .footer-wave {
    position: absolute; left: 0; bottom: 0; width: 735px; height: 88px;
  }
</style>
</head>
<body>
  <main class="letterhead">
    <div class="brand-name">Harbor Loom Floors</div>

    <address class="contact">
      <div class="address">2715 W. Pelican Lane<br>Marlow Cove SC 34187</div>
      <div class="phone">
        <svg viewBox="0 0 24 24" aria-hidden="true"><path fill="var(--brand-orange)" d="M6.6 10.8a15.1 15.1 0 0 0 6.6 6.6l2.2-2.2c.3-.3.7-.4 1-.2 1.1.4 2.3.6 3.6.6.6 0 1 .4 1 1V20c0 .6-.4 1-1 1A17 17 0 0 1 3 4c0-.6.4-1 1-1h3.5c.6 0 1 .4 1 1 0 1.3.2 2.5.6 3.6.1.3 0 .7-.2 1z"/></svg>
        <span>555.382.6519</span>
      </div>
    </address>

    <section class="letter-body">
      <p class="date">January-03-2020</p>
      <p class="recipient">Mr, Paul Reyes<br>President</p>
      <p class="recipient-company">Crestline Partners<br>123 Street Name, Suite# 10<br>City, State, 120023</p>
      <p class="salutation">Dear Mr, Paul</p>
      <p class="paragraph">Lorem ipsum dolor sit amet, consectetur adipiscing elit, sed do eiusmod tempor incididunt ut labore et dolore magna aliqua. Ut enim ad minim veniam, quis nostrud exercitation ullamco laboris nisi ut aliquip ex ea commodo consequat. Duis aute irure dolor in reprehenderit in voluptate velit esse cillum dolore eu fugiat nulla pariatur.</p>
      <p class="paragraph">Lorem ipsum dolor sit amet, consectetur adipiscing elit, sed do eiusmod tempor incididunt ut labore et dolore magna aliqua. Ut enim ad minim veniam, quis nostrud exercitation ullamco laboris nisi ut aliquip ex ea commodo consequat. Duis aute irure dolor in reprehenderit in voluptate velit esse cillum dolore eu fugiat nulla pariatur.</p>
      <p class="paragraph">Lorem ipsum dolor sit amet, consectetur adipiscing elit, sed do eiusmod tempor incididunt ut labore et dolore magna aliqua. Ut enim ad minim veniam, quis nostrud exercitation ullamco laboris nisi ut aliquip ex ea commodo consequat.</p>
      <p class="paragraph">Excepteur sint occaecat cupidatat non proident, sunt in culpa qui officia deserunt mollit anim id est laborum. re et dolore magnam aliquam quaerat voluptatem.</p>
      <p class="closing">Regards</p>
    </section>

    <p class="signature">Dana Whitfield</p>

    <svg class="footer-wave" viewBox="0 1300 1004 120" preserveAspectRatio="none" aria-hidden="true">
      <path fill="var(--brand-orange)" d="M0 1310 Q 430 1430 1004 1368 V1420 H0 Z"/>
      <path fill="var(--brand-gray)" d="M330 1364 Q 700 1378 1004 1327 V1355 Q 700 1386 330 1364 Z"/>
    </svg>
  </main>
</body>
</html>
```